An e-flyer for an exotic car and fine wine club.

This is the first meeting of Birchwell Motor Society and includes several businesses. Their logos should be featured at the bottom. It should be sleek, elegant and simple featuring a photo of an Varenne Coupe R7 as well as my logo (I will provide photos). The flyer needs to look professional and appeal to billionaires.
The text should read:
Birchwell Motor society presents
Quick Wheels and Rare Vintages (but not while driving)
Hosted by Halvorn Keep Vault
Bring your best car(s) and join us to enjoy the party with sommelier selected wines, the best classic and modern cars and hors d'oeuvre catered by Pembry's Shellfish Bar. Live DJ.
August 26th 3-6 p.m.
This event is gratis.
RSVP to nora@birchwellmotors.example for address and details

Target Market(s)
Very wealthy exotic car owners
Industry/Entity Type
Car Club, Fine Wines.
Requirements
Must have
- Style, panache, elegance, sleekness, simplicity. I like the idea of a black or dark flyer with a consistent color scheme.
Nice to have
- I want the flyer to be simple and sleek, feature an Varenne Coupe R7 as the eye catcher, Birchwell Motor Society logo featured prominently on the top, and the other business logos on the bottom.
Should not have
- It must not be too noisy or busy.

```html
<!DOCTYPE html>
<html lang="en">
<head>
<meta charset="utf-8">
<title>Quick Wheels &amp; Rare Vintages — Birchwell Motor Society</title>
<link rel="stylesheet" href="https://fonts.googleapis.com/css2?family=Arimo:wght@400;700&family=Russo+One&family=Oswald:wght@500&family=Montserrat:wght@600&display=swap">
<style>
  :root {
    --charcoal: #404040;
    --crimson: #c4283f;
    --crimson-light: #e0445a;
    --car-red: #a51f32;
    --car-deep: #6e1421;
    --white: #ffffff;
    --silver: #a9a9a9;
    --text-light: #f2f2f2;
  }
  * { margin: 0; padding: 0; box-sizing: border-box; }
  html, body { width: 849px; height: 1200px; overflow: hidden; }
  body {
    background: var(--charcoal);
    font-family: "Arimo", Arial, sans-serif;
    color: var(--text-light);
    position: relative;
  }
  .flyer { position: relative; width: 849px; height: 1200px; }

  .club-name {
    position: absolute; top: 112px; left: 0; width: 100%;
    text-align: center;
    font-family: "Montserrat", sans-serif; font-weight: 600;
    color: var(--white);
    font-size: 26px; letter-spacing: 6px; line-height: 36px;
    text-transform: uppercase;
  }
  .presents {
    position: absolute; top: 198px; left: 0; width: 100%;
    text-align: center;
    font-family: "Arimo", sans-serif; font-weight: 700;
    font-size: 11px; letter-spacing: 14px; color: var(--silver);
    padding-left: 14px;
  }

  .headline-panel {
    position: absolute; top: 227px; left: 237px;
    width: 374px; height: 393px;
    background: var(--crimson);
  }
  .headline-art { position: absolute; left: 0; top: 0; }
  .kicker { font-family: "Montserrat", sans-serif; font-weight: 600; fill: var(--white); }
  .display { font-family: "Russo One", sans-serif; fill: var(--white); }

  .tagline {
    position: absolute; top: 521px; left: 237px; width: 374px;
    text-align: center; font-weight: 700; font-size: 11.5px; color: var(--white);
  }
  .host {
    position: absolute; top: 539px; left: 237px; width: 374px;
    text-align: center; font-weight: 700; font-size: 17.5px; color: var(--white);
  }

  .hero-photo {
    position: absolute; top: 566px; left: 128px;
    width: 594px; height: 182px;
    background: linear-gradient(180deg, var(--car-red) 0%, var(--car-deep) 100%);
  }

  .details {
    position: absolute; top: 758px; left: 247px; width: 354px;
    font-size: 13.6px; line-height: 21px;
    text-align: justify; text-align-last: justify;
  }
  .live-dj {
    position: absolute; top: 824px; left: 0; width: 100%;
    text-align: center; color: var(--crimson);
    font-weight: 700; font-size: 25px;
  }

  .date-band {
    position: absolute; top: 866px; left: 237px; width: 374px; height: 58px;
    background: var(--crimson);
    display: flex; align-items: center; justify-content: center;
    font-family: "Oswald", sans-serif; font-weight: 500;
    font-size: 41px; color: var(--white); letter-spacing: 0.5px;
  }
  .date-band sup { font-size: 19px; vertical-align: 18px; margin-right: 12px; }

  .rsvp {
    position: absolute; top: 938px; left: 0; width: 100%;
    text-align: center; font-size: 13.6px; line-height: 21px;
  }

  .partners {
    position: absolute; top: 1015px; left: 237px; width: 374px; height: 110px;
    display: flex; gap: 3px;
  }
  .partner {
    flex: 1; background: var(--white);
    border-top: 2px solid var(--crimson); border-bottom: 2px solid var(--crimson);
    display: flex; align-items: center; justify-content: center;
    text-align: center; padding: 0 12px;
    font-family: "Arimo", sans-serif; font-weight: 700; font-size: 15px; line-height: 19px;
  }
  .partner-vault { color: var(--crimson); }
  .partner-cellars { color: #222222; }
</style>
</head>
<body>
<main class="flyer">
  <header>
    <p class="club-name">Birchwell<br>Motor Society</p>
    <p class="presents">PRESENTS</p>
  </header>

  <section class="headline-panel" aria-label="Quick Wheels and Rare Vintages">
    <svg class="headline-art" width="374" height="393" viewBox="0 0 374 393">
      <g stroke="var(--white)" stroke-width="0.8">
        <line x1="52" y1="45" x2="142" y2="45"/><line x1="52" y1="49" x2="142" y2="49"/><line x1="52" y1="53" x2="142" y2="53"/>
        <line x1="232" y1="45" x2="322" y2="45"/><line x1="232" y1="49" x2="322" y2="49"/><line x1="232" y1="53" x2="322" y2="53"/>
        <line x1="52" y1="184" x2="142" y2="184"/><line x1="52" y1="188" x2="142" y2="188"/><line x1="52" y1="192" x2="142" y2="192"/>
        <line x1="232" y1="184" x2="322" y2="184"/><line x1="232" y1="188" x2="322" y2="188"/><line x1="232" y1="192" x2="322" y2="192"/>
      </g>
      <text class="kicker" x="187" y="57" text-anchor="middle" font-size="20" letter-spacing="3">QUICK</text>
      <text class="display" x="45" y="148" font-size="104" textLength="284" lengthAdjust="spacingAndGlyphs">WHEELS</text>
      <line x1="57" y1="163" x2="317" y2="163" stroke="var(--white)" stroke-width="3" stroke-linecap="round" stroke-dasharray="0 6.5"/>
      <circle cx="187" cy="163" r="9" fill="var(--crimson)"/>
      <text class="kicker" x="187" y="169" text-anchor="middle" font-size="15">&amp;</text>
      <text class="kicker" x="187" y="196" text-anchor="middle" font-size="20" letter-spacing="3">RARE</text>
      <text class="display" x="45" y="288" font-size="104" textLength="284" lengthAdjust="spacingAndGlyphs">VINTAGES</text>
      <line x1="44" y1="300" x2="110" y2="300" stroke="var(--crimson-light)" stroke-width="4"/>
      <line x1="264" y1="300" x2="330" y2="300" stroke="var(--crimson-light)" stroke-width="4"/>
    </svg>
  </section>
  <p class="tagline">BUT NOT WHILE DRIVING</p>
  <p class="host">HOSTED BY HALVORN KEEP VAULT</p>

  <div class="hero-photo" role="img" aria-label="Side profile photo of a red Varenne Coupe R7 classic sports car"></div>

  <p class="details">Bring your best car(s) and join us to enjoy the party with sommelier selected wines, the best classic and modern cars and hors d'oeuvre catered by Pembry's Shellfish Bar.</p>
  <p class="live-dj">Live DJ.</p>

  <div class="date-band">AUGUST 26<sup>TH</sup>3-6 P.M.</div>

  <p class="rsvp">THIS EVENT IS GRATIS.<br>RSVP to nora@birchwellmotors.example<br>for address and details</p>

  <footer class="partners">
    <div class="partner partner-vault">Halvorn Keep Vault</div>
    <div class="partner partner-cellars">Marlowe Street Cellars</div>
  </footer>
</main>
</body>
</html>
```